DL FLYER - Stroll Sip Nibble Trails

I need a2-sided DL flyer designed to put into Hotel foyers. This will need to stand out as it will be in a rack with multiple other options.

Our tours are all about walking with us to take in great venues for food and beverages with art and history along the way.

We operate in Perth City plus Fremantle.

I am hoping for the flyer to look something like my website - https://strollsipnibble.example.au/

This website will be updated in the coming weeks with new experiences and a new booking platform.

I want the flyers to be used to drive bookings from the updated website.

Attached are several images that could be used also.

Target Market(s)

Social groups, couples, friends groups & foodies!

Industry/Entity Type

Food & Beverage Walking Tours

Font styles to use
Serif
Sans Serif
Decorative
Script

Colors
0094D4
00A9DD
6FCCEA
C7EBF8
E9F6FB
59FF00
82FF00
B8FF75
E3FFCB
F4FFEA
FFF300
FFF600
FEFA6F
FFFEC7
FFFEE8
F0912C
F2A743
F7CA91
FBE8D2
FDF5EE

Requirements
Must have
• Logo and must look fun. Discount code - GOODVIBES for online price 15% off (not valid on gift voucher purchases)
Nice to have
• similar to my website - colours and styling. I will be updating available tours, costs and timing in the coming weeks. Check out my new booking link to get pricing and tour details - https://www-628q.reservly.example/reservly/b_strollsipnibbletrails_start.html?ctlsrc2=Qm482KTRVA9LZpd7JowsN3hbvY%2F5U8RaxtnBd%2FJqLm%3D&src=02r
Should not have
• .

```html
<!DOCTYPE html>
<html lang="en">
<head>
<meta charset="utf-8">
<title>Stroll Sip Nibble Trails – DL Flyer</title>
<link rel="stylesheet" href="https://fonts.googleapis.com/css2?family=Oswald:wght@600&family=Caveat+Brush&family=Montserrat:wght@400;600;700&display=swap">
<style>
  :root{
    --bg:#d3d6d3;
    --cream:#efebd4;
    --green:#8dc08e;
    --green-text:#8fcf90;
    --teal:#173f38;
    --orange:#e5622a;
    --peach:#ee9c68;
    --ink:#1d1b1b;
    --rule:#9a9a8c;
  }
  *{box-sizing:border-box;margin:0;padding:0}
  html,body{width:1200px;height:1200px;overflow:hidden}
  body{background:var(--bg);font-family:"Montserrat",sans-serif;color:var(--ink);display:flex;justify-content:center;align-items:center;gap:44px}
  .flyer{position:relative;width:520px;height:1100px;background:var(--cream);overflow:hidden}
  .brand{display:flex;flex-direction:column;align-items:center;gap:10px}
  .brand-dot{width:70px;height:70px;border-radius:50%;background:var(--peach)}
  .brand-name{font-family:"Oswald",sans-serif;font-weight:600;color:var(--teal);font-size:34px;line-height:1.05;text-align:center;letter-spacing:.3px}
  .script{font-family:"Caveat Brush",cursive}
  .footer{position:absolute;left:0;right:0;bottom:0;height:108px;background:var(--ink);display:flex;align-items:center;padding:0 22px;gap:14px;color:#f2f2ee}
  .footer .label{font-weight:700;color:var(--green-text);font-size:20px;white-space:nowrap}
  .footer .details{font-size:11px;line-height:1.55}
  .footer .divider{width:1px;height:60px;background:#777}
  .footer .follow{display:flex;flex-direction:column;gap:6px;font-size:11px}
  .footer .follow .label{font-size:16px}
  .social{display:flex;align-items:center;gap:5px}
  .social i{width:10px;height:10px;border-radius:50%;background:#f2f2ee;display:inline-block}
  .discount{text-align:center;color:var(--teal);font-size:22px;line-height:1.35}

  /* front */
  .front .brand{position:absolute;top:36px;left:0;right:0}
  .front .intro{position:absolute;top:208px;left:50px;right:50px;text-align:center;font-size:23px;line-height:1.2;color:var(--teal)}
  .hero{position:absolute;top:310px;left:110px;width:300px;height:260px;border-radius:50%;background:radial-gradient(circle at 40% 40%,#f4c8b4 0%,#d9e8b8 45%,#8dc08e 80%,var(--cream) 100%)}
  .features{position:absolute;top:600px;left:20px;right:20px;display:flex;justify-content:space-around;list-style:none}
  .feature{display:flex;flex-direction:column;align-items:center;gap:8px}
  .feature-icon{width:52px;height:44px;border-radius:50% 50% 50% 10%;background:var(--green);display:flex;align-items:center;justify-content:center}
  .feature-label{background:#e4e2d2;border-radius:12px;padding:5px 14px;font-size:9.5px;font-weight:700;letter-spacing:.2px}
  .section-title{position:absolute;top:718px;left:0;right:0;text-align:center;font-size:34px;letter-spacing:.5px;font-weight:400}
  .section-title span{background:linear-gradient(transparent 45%,var(--green) 45%,var(--green) 85%,transparent 85%);padding:0 6px}
  .band{position:absolute;top:830px;left:0;right:0;height:170px;background:var(--green)}
  .photos{position:absolute;top:770px;left:42px;right:42px;display:flex;justify-content:space-between}
  .photo{width:130px;height:120px;border-radius:22px;border:5px solid var(--cream)}
  .photo-1{background:linear-gradient(135deg,#6d3a4a,#c7a7b0 55%,#5c4a3a)}
  .photo-2{background:linear-gradient(135deg,#e8d2c4,#b98a7a 50%,#5a2a2e)}
  .photo-3{background:linear-gradient(135deg,#2f5a80,#b48a5a 55%,#e3a06c)}
  .front .discount{position:absolute;top:912px;left:10px;right:10px}

  /* back */
  .back .title{position:absolute;top:34px;left:0;right:0;text-align:center;font-size:36px;font-weight:400}
  .back .title span{background:linear-gradient(transparent 25%,var(--green) 25%,var(--green) 90%,transparent 90%);padding:0 8px;border-radius:14px}
  .back .subtitle{position:absolute;top:96px;left:0;right:0;text-align:center;font-weight:600;font-size:17px}
  .schedule{position:absolute;top:136px;left:30px;right:30px;font-size:10.5px}
  .schedule .head,.schedule .row{display:grid;grid-template-columns:34px 120px 1fr 70px 44px;align-items:center}
  .schedule .head{font-size:8px;font-weight:700;padding-bottom:5px;border-bottom:1px solid var(--rule)}
  .schedule .day{font-weight:700;font-size:11px;padding:8px 0 2px}
  .schedule .row{padding:6px 0;border-bottom:1px solid var(--rule)}
  .schedule .row b{font-weight:700}
  .thumb{width:22px;height:18px;background:linear-gradient(135deg,#c7763a,#f0c38a)}
  .center{text-align:center}
  .booking{position:absolute;top:566px;left:0;right:0;text-align:center}
  .booking .pill{display:inline-block;background:var(--green);border-radius:12px;padding:2px 14px;font-size:22px;color:var(--teal)}
  .booking .url{margin-top:10px;font-size:13px;letter-spacing:4px}
  .back .brand{position:absolute;top:660px;left:0;right:0}
  .back .brand-dot{width:90px;height:90px}
  .back .brand-name{font-size:40px}
  .back .discount{position:absolute;top:890px;left:10px;right:10px;font-size:20px}
  .back .discount .pill{display:inline-block;background:var(--green);border-radius:14px;padding:0 14px;font-size:23px}
</style>
</head>
<body>

<section class="flyer front">
  <div class="brand">
    <span class="brand-dot"></span>
    <div class="brand-name">Stroll Sip Nibble Trails</div>
  </div>

  <p class="intro script">Our tours are all about walking with us to take in great venues for food and beverages with art and history along the way.</p>

  <div class="hero" role="img" aria-label="Illustration of a tour group walking in front of the city skyline under an orange sun"></div>

  <ul class="features">
    <li class="feature">
      <span class="feature-icon"><svg width="20" height="24" viewBox="0 0 20 24"><path d="M10 2a7 7 0 0 0-7 7c0 5 7 13 7 13s7-8 7-13a7 7 0 0 0-7-7z" fill="none" stroke="#e5622a" stroke-width="2"/><circle cx="10" cy="9" r="2.5" fill="#e5622a"/></svg></span>
      <span class="feature-label">EXPLORE THE CITY</span>
    </li>
    <li class="feature">
      <span class="feature-icon"><svg width="26" height="22" viewBox="0 0 26 22"><path d="M13 2C6.9 2 2 5.9 2 10.5c0 2.3 1.2 4.4 3.2 5.9L4 20l4.4-2.2c1.4.5 3 .7 4.6.7 6.1 0 11-3.9 11-8.5S19.1 2 13 2z" fill="none" stroke="#e5622a" stroke-width="2"/><circle cx="8" cy="10.5" r="1.6" fill="#e5622a"/><circle cx="13" cy="10.5" r="1.6" fill="#e5622a"/><circle cx="18" cy="10.5" r="1.6" fill="#e5622a"/></svg></span>
      <span class="feature-label">MEET NEW PEOPLE</span>
    </li>
    <li class="feature">
      <span class="feature-icon"><svg width="28" height="22" viewBox="0 0 28 22"><path d="M3 12h22a11 7 0 0 1-22 0z" fill="none" stroke="#e5622a" stroke-width="2"/><path d="M10 8c-1-2 1-3 0-5M15 8c-1-2 1-3 0-5" fill="none" stroke="#e5622a" stroke-width="1.8" stroke-linecap="round"/></svg></span>
      <span class="feature-label">ENJOY GREAT FOOD</span>
    </li>
  </ul>

  <h2 class="section-title script"><span>TOURS &amp; EXPERIENCES</span></h2>

  <div class="band"></div>
  <div class="photos">
    <div class="photo photo-1" role="img" aria-label="Photo of cocktails on a bar table"></div>
    <div class="photo photo-2" role="img" aria-label="Photo of guests enjoying red wine together"></div>
    <div class="photo photo-3" role="img" aria-label="Photo of a shared meal with wine being poured"></div>
  </div>

  <p class="discount script">Discount code - GOODVIBES<br>for online price 15% off (not valid on gift voucher purchases)</p>

  <footer class="footer">
    <span class="label">Contact Us</span>
    <div class="details">0400 123 456<br>perth@strollsipnibble.example.au<br>Daily: 8:00 am – 6:00 pm</div>
    <span class="divider"></span>
    <div class="follow">
      <span class="label">Follow us</span>
      <span class="social"><i></i>Socialoop <i></i>Picstream</span>
    </div>
  </footer>
</section>

<section class="flyer back">
  <h1 class="title script"><span>Stroll Sip Nibble Trails</span></h1>
  <p class="subtitle">Available Tours</p>

  <div class="schedule">
    <div class="head"><span>Time</span><span></span><span>Tour</span><span class="center">Available</span><span class="center">Price</span></div>

    <div class="day">Thursday</div>
    <div class="row"><span class="thumb" role="img" aria-label="Tour thumbnail photo"></span><span>5:30 PM - 8:30 PM</span><b>Weeknight Street Eats</b><span class="center">12</span><span class="center">$79</span></div>

    <div class="day">Saturday</div>
    <div class="row"><span class="thumb" role="img" aria-label="Tour thumbnail photo"></span><span>12:00 PM - 3:30 PM</span><b>Laneway Long Lunch</b><span class="center">14</span><span class="center">$92</span></div>
    <div class="row"><span class="thumb" role="img" aria-label="Tour thumbnail photo"></span><span>11:30 AM - 2:30 PM</span><b>Cosy Cellar Crawl</b><span class="center">14</span><span class="center">$89</span></div>
    <div class="row"><span class="thumb" role="img" aria-label="Tour thumbnail photo"></span><span>2:00 PM - 5:30 PM</span><b>Brews &amp; Bites</b><span class="center">18</span><span class="center">$88</span></div>
    <div class="row"><span></span><span>4:30 PM - 8:30 PM</span><b>Golden Hour Supper</b><span class="center">18</span><span class="center">$105</span></div>

    <div class="day">Sunday</div>
    <div class="row"><span class="thumb" role="img" aria-label="Tour thumbnail photo"></span><span>10:30 AM - 1:30 PM</span><b>Cosy Cellar Crawl</b><span class="center">14</span><span class="center">$89</span></div>
    <div class="row"><span class="thumb" role="img" aria-label="Tour thumbnail photo"></span><span>2:30 PM - 6:30 PM</span><b>Slow Sunday by the Port</b><span class="center">12</span><span class="center">$102</span></div>

    <div class="day">Wednesday</div>
    <div class="row"><span class="thumb" role="img" aria-label="Tour thumbnail photo"></span><span>5:30 PM - 8:30 PM</span><b>Weeknight Street Eats</b><span class="center">12</span><span class="center">$79</span></div>
  </div>

  <div class="booking">
    <span class="pill script">BOOKING NOW</span>
    <p class="url">www.strollsipnibble.example.au</p>
  </div>

  <div class="brand">
    <span class="brand-dot"></span>
    <div class="brand-name">Stroll Sip Nibble Trails</div>
  </div>

  <p class="discount script"><span class="pill">Discount code - GOODVIBES</span><br>for online price 15% off (not valid on gift voucher purchases)</p>

  <footer class="footer">
    <span class="label">Contact Us</span>
    <div class="details">0400 123 456<br>hello@strollsipnibble.example.au<br>www.strollsipnibble.example.au</div>
    <span class="divider"></span>
    <div class="follow">
      <span class="label">Follow us</span>
      <span class="social"><i></i>Socialoop <i></i>Picstream</span>
    </div>
  </footer>
</section>

</body>
</html>
```